Venture 482 - Lumora Book Cover

I am looking for a Lumora book cover for my book about "Venture 482".
The Book is Titled:
Venture 482 Ascended
Shaping Outcomes: Paths To Unlocking Cosmic Truths
Author is Dorian Pell
Here is a book description that may help you understand more about it:
Inspired by the genius of Edwin Marlowe, this comprehensive guide delves into the ancient wisdom and cutting-edge science behind the 482 method, a powerful tool for manifesting your desires. Whether you're seeking personal growth, financial success, or spiritual enlightenment, this book provides advanced techniques and methods to transform your dreams into reality.
Any questions please ask.
Thanks
Owen

```html
<!DOCTYPE html>
<html lang="en">
<head>
<meta charset="utf-8">
<title>Venture 482 Ascended — Dorian Pell</title>
<link rel="stylesheet" href="https://fonts.googleapis.com/css2?family=Cinzel:wght@400;600;700;900&family=Montserrat:wght@300&family=Tinos&display=swap">
<style>
  :root {
    --sky-deep: #1c4a82;
    --sky-mid: #4f86c0;
    --sky-light: #a9c6e0;
    --haze: #dfe1e4;
    --land: #a89a86;
    --floor-light: #cfc3b4;
    --floor-dark: #3e3a36;
    --title-cream: #f7e7dc;
    --subtitle-cream: #fdf8df;
    --line-white: #ffffff;
    --shadow-soft: rgba(40, 50, 70, 0.45);
    --shadow-hard: rgba(20, 20, 20, 0.9);
  }
  html, body {
    margin: 0;
    padding: 0;
    overflow: hidden;
    background: #ffffff;
  }
  .cover {
    position: relative;
    width: 805px;
    height: 1200px;
    overflow: hidden;
  }
  .cover-scene {
    position: absolute;
    inset: 0;
    background: linear-gradient(to bottom,
      var(--sky-deep) 0%,
      var(--sky-mid) 28%,
      var(--sky-light) 52%,
      var(--haze) 63%,
      var(--land) 66%,
      #c9b8a2 70%,
      var(--floor-light) 74%,
      #a89d90 86%,
      var(--floor-dark) 100%);
  }
  .cover-text {
    position: absolute;
    left: 0;
    width: 100%;
    margin: 0;
    text-align: center;
    line-height: 1;
  }
  .author {
    top: 84px;
    font-family: "Cinzel", serif;
    font-weight: 400;
    font-size: 46px;
    letter-spacing: 0.34em;
    padding-left: 0.34em;
    box-sizing: border-box;
    color: var(--title-cream);
  }
  .title-word {
    top: 180px;
    font-family: "Cinzel", serif;
    font-weight: 700;
    font-size: 104px;
    color: var(--title-cream);
    text-shadow: 6px 8px 10px var(--shadow-soft);
  }
  .title-number {
    top: 290px;
    font-family: "Cinzel", serif;
    font-weight: 700;
    font-size: 250px;
    letter-spacing: -0.02em;
    color: var(--title-cream);
    text-shadow: 8px 10px 14px var(--shadow-soft);
  }
  .edition {
    top: 540px;
    font-family: "Cinzel", serif;
    font-weight: 900;
    font-size: 46px;
    letter-spacing: 0.42em;
    padding-left: 0.42em;
    box-sizing: border-box;
    color: var(--subtitle-cream);
    text-shadow: 3px 3px 0 var(--shadow-hard);
  }
  .tagline {
    top: 1033px;
    font-family: "Montserrat", sans-serif;
    font-weight: 300;
    font-size: 29px;
    letter-spacing: 0.01em;
    color: var(--line-white);
  }
  .subtitle {
    top: 1087px;
    font-family: "Tinos", serif;
    font-weight: 400;
    font-size: 27px;
    line-height: 35px;
    color: var(--line-white);
  }
</style>
</head>
<body>
  <main class="cover">
    <div class="cover-scene" role="img" aria-label="Photographic scene: a person seen from behind standing barefoot on a pale stone terrace, looking out over a wide desert plain under a blue sky with white clouds"></div>
    <p class="cover-text author">Dorian Pell</p>
    <h1 class="cover-text title-word">VENTURE</h1>
    <p class="cover-text title-number">482</p>
    <p class="cover-text edition">ASCENDED</p>
    <p class="cover-text tagline">SHAPING OUTCOMES:</p>
    <p class="cover-text subtitle">Paths to unlocking<br>cosmic truths</p>
  </main>
</body>
</html>
```